Brindle Sky Port needs a new upscale business card design for our high end aircraft hangar complex

Brindle Sky Port (BSP) is a large, upscale jet hangar complex in the US housing expensive aircraft. We need a new business card design, using our current logo. We will be attending a industry convention and need a card design that will stand out and be remembered by aircraft owners and private pilots.

Target Market(s)

Aircraft pilots or owners looking for a new upscale hangar

Industry/Entity Type

Airport

Contact Information for Business Card

I like to use very heavy card stock, 400#, double sided. Square, no rounded edges please.

Colors
3276b5
0255a3
85abd2

Requirements
Must have
• An expensive, classy design, vivid colors.
Nice to have
• Needs to look very expensive and classy, and have some "pop". Designer must be able to download or copy my current typeface or fonts.
• One card side might be black with the "Logo and Brindle Sky Port Double line image in blue (or try gold, or glossy black), and perhaps have a grayed out "K720 jet silhouette". The other card side would have our contact info, and perhaps the "BSP Logo only". I'd like my contact info 'stacked', not in a paragraph format.
Should not have
• Should not look "too busy". Having a double-sided card will help.

```html
<!DOCTYPE html>
<html lang="en">
<head>
<meta charset="utf-8">
<title>Brindle Sky Port – Business Card</title>
<link href="https://fonts.googleapis.com/css2?family=Arimo:wght@400;700&display=swap" rel="stylesheet">
<style>
  :root {
    --backdrop: #3a3532;
    --card-black: #1c1c1e;
    --silver: #b9b9bd;
    --blue: #3276b5;
    --blue-deep: #0255a3;
    --blue-light: #85abd2;
    --white: #f2f2f2;
    --rule: #d8d8d8;
  }
  * { margin: 0; padding: 0; box-sizing: border-box; }
  html, body { width: 1200px; height: 787px; overflow: hidden; }
  body {
    background: var(--backdrop);
    font-family: "Arimo", Arial, sans-serif;
    position: relative;
  }
  .card {
    position: absolute;
    width: 540px;
    height: 309px;
    background: var(--card-black);
    top: 239px;
  }
  .card--front { left: 40px; }
  .card--back { left: 620px; }

  /* Front side */
  .front-brand {
    position: absolute;
    left: 0; right: 0; top: 92px;
    text-align: center;
    color: var(--silver);
    font-weight: 700;
  }
  .front-brand__mark {
    display: inline-block;
    width: 14px; height: 14px;
    background: var(--silver);
    vertical-align: middle;
    margin-right: 12px;
  }
  .front-brand__name {
    font-size: 34px;
    letter-spacing: 1px;
    vertical-align: middle;
  }
  .front-web {
    position: absolute;
    left: 0; right: 0; top: 200px;
    text-align: center;
    color: var(--white);
    font-size: 13px;
    letter-spacing: 3px;
  }

  /* Back side */
  .contact {
    position: absolute;
    left: 34px; top: 46px;
    color: var(--white);
  }
  .contact__name { color: var(--blue); font-size: 18px; }
  .contact__title { font-size: 14px; margin-top: 2px; }
  .contact__list { list-style: none; margin-top: 14px; font-size: 13px; }
  .contact__list li { display: flex; align-items: center; height: 19px; }
  .contact__list svg { width: 12px; height: 12px; margin-right: 12px; fill: var(--blue); }
  .rule {
    position: absolute;
    height: 1px;
    background: var(--rule);
  }
  .rule--middle { left: 150px; right: 0; top: 124px; }
  .rule--lower { left: 290px; right: 22px; top: 222px; }
  .back-brand {
    position: absolute;
    right: 26px; top: 80px;
    color: var(--blue);
    font-weight: 700;
    font-size: 22px;
    display: flex; align-items: center;
  }
  .back-brand__mark {
    width: 12px; height: 12px;
    background: var(--blue);
    margin-right: 10px;
  }
  .address {
    position: absolute;
    right: 22px; top: 236px;
    text-align: right;
    color: var(--white);
    font-size: 13px;
    line-height: 19px;
  }
  .address__web { letter-spacing: 2.5px; }
</style>
</head>
<body>
  <section class="card card--front" aria-label="Card front">
    <div class="front-brand">
      <span class="front-brand__mark"></span><span class="front-brand__name">Brindle Sky Port</span>
    </div>
    <p class="front-web">www.brindlesky.com</p>
  </section>

  <section class="card card--back" aria-label="Card back">
    <div class="contact">
      <p class="contact__name">Dale Marsh</p>
      <p class="contact__title">President</p>
      <ul class="contact__list">
        <li><svg viewBox="0 0 12 12"><path d="M1 3c0-1 1-2 2-2h6c1 0 2 1 2 2v1H8V3H4v1H1zM2 5h8l1 6H1z"/></svg>555 0147 2260</li>
        <li><svg viewBox="0 0 12 12"><path d="M3 0h6v12H3zM4 1v8h4V1z"/></svg>555 0193 4418</li>
        <li><svg viewBox="0 0 12 12"><path d="M3 0h6v4H3zM1 5h10v5H9v2H3v-2H1z"/></svg>555 0162 7731</li>
        <li><svg viewBox="0 0 12 12"><path d="M0 2h12v1L6 7 0 3zM0 4l6 4 6-4v6H0z"/></svg>dale@brindlesky.com</li>
      </ul>
    </div>
    <div class="rule rule--middle"></div>
    <div class="back-brand"><span class="back-brand__mark"></span>Brindle Sky Port</div>
    <div class="rule rule--lower"></div>
    <div class="address">
      <p>2160 Alder Ridge Road</p>
      <p>Millbrook, NY 12545</p>
      <p class="address__web">www.brindlesky.com</p>
    </div>
  </section>
</body>
</html>
```